****Business Card Design for Quarrystone Development. Design based around attached logo/company name

I’m looking for business card design for my company Quarrystone Development Group,LLC. Design should be professional, sharp and minimal. Outside of the attached logos, greyscale colors for remainder of cards. My thoughts are two-sided card with attached logo on one side and my info on the other but open to one-sided as well with right design.
Target Market(s)
Real estate professionals including banks, private investors, property owners, developers, commercial tenants like Brewlantern, Grovika or Tanquist’s.
Industry/Entity Type
Commercial real estate development and investments.
Contact Information for Business Card
Name, title, email, phone #’s, web address and physical address
Font styles to use
Other font styles liked:
- Helvetica, Garamond, etc
Colors
Designer to choose only greyscale colors for use in the design.
Requirements
Must have
- Attached logo first or second options.
Nice to have
- Two sided card with logo on one side. Attached Logo/company name can be laid out any way that flows as long as it’s legible.name
Should not have
- No loud colors. ***Please do not include logo, I have removed the company design with a logo image.

```html
<!DOCTYPE html>
<html lang="en">
<head>
<meta charset="utf-8">
<title>Quarrystone Development Group, LLC — Business Card</title>
<link href="https://fonts.googleapis.com/css2?family=Tinos&display=swap" rel="stylesheet">
<style>
  :root {
    --page: #e6e6e6;
    --card-top: #6f7686;
    --card-bottom: #565d6c;
    --ink: #ffffff;
    --rule: rgba(255,255,255,0.45);
    --band-light: #ffffff;
    --band-grey: #9a9ca2;
  }
  html, body {
    margin: 0;
    width: 1200px;
    height: 1200px;
    overflow: hidden;
    background: var(--page);
    font-family: "Tinos", "Times New Roman", serif;
    color: var(--ink);
  }
  .card {
    position: absolute;
    left: 257px;
    width: 686px;
    height: 392px;
    background: linear-gradient(170deg, var(--card-top), var(--card-bottom));
    overflow: hidden;
  }
  .card--front { top: 165px; }
  .card--back { top: 643px; }

  .wordmark {
    position: absolute;
    left: 80px;
    top: 166px;
    width: 240px;
    text-align: right;
    line-height: 1;
  }
  .wordmark__name { font-size: 31px; letter-spacing: 0.5px; display: block; }
  .wordmark__sub { font-size: 11.5px; letter-spacing: 0.3px; display: block; margin-top: 4px; }

  .divider {
    position: absolute;
    left: 357px;
    top: 96px;
    width: 1px;
    height: 206px;
    background: linear-gradient(to bottom, transparent, var(--rule) 20%, var(--rule) 80%, transparent);
  }

  .contact {
    position: absolute;
    left: 386px;
    top: 104px;
    font-size: 16px;
    line-height: 1.25;
  }
  .contact__name { font-size: 22px; letter-spacing: 0.5px; margin: 0; font-weight: 400; }
  .contact__title { margin: 0 0 12px; }
  .contact__address { margin: 0 0 12px; font-style: normal; }
  .contact__list { list-style: none; margin: 0; padding: 0; }
  .contact__list li { display: flex; align-items: center; height: 20.5px; }
  .contact__list svg { width: 13px; height: 13px; margin-right: 12px; fill: var(--ink); flex: none; }

  .band {
    position: absolute;
    left: 0;
    bottom: 0;
    width: 686px;
    height: 13px;
  }

  .back-mark {
    position: absolute;
    left: 0;
    right: 0;
    top: 158px;
    text-align: center;
    line-height: 1;
  }
  .back-mark__name { font-size: 40px; letter-spacing: 2px; display: block; }
  .back-mark__sub { font-size: 13px; letter-spacing: 2px; display: block; margin-top: 8px; }

  .back-url {
    position: absolute;
    left: 0;
    right: 0;
    top: 316px;
    text-align: center;
    font-size: 15px;
    letter-spacing: 7px;
  }
</style>
</head>
<body>

<section class="card card--front" aria-label="Card front">
  <div class="wordmark">
    <span class="wordmark__name">QUARRYSTONE</span>
    <span class="wordmark__sub">DEVELOPMENT GROUP, LLC</span>
  </div>

  <div class="divider"></div>

  <div class="contact">
    <h1 class="contact__name">DANIEL HARROW</h1>
    <p class="contact__title">President</p>
    <address class="contact__address">4120 Birchmont Lane<br>Fairhaven, Alaska 99517</address>
    <ul class="contact__list">
      <li><svg viewBox="0 0 24 24" aria-hidden="true"><path d="M6.6 10.8a15.2 15.2 0 0 0 6.6 6.6l2.2-2.2c.3-.3.7-.4 1-.2 1.1.4 2.3.6 3.6.6.6 0 1 .4 1 1V20c0 .6-.4 1-1 1A17 17 0 0 1 3 4c0-.6.4-1 1-1h3.5c.6 0 1 .4 1 1 0 1.3.2 2.5.6 3.6.1.3 0 .7-.2 1z"/></svg>555-214-7730</li>
      <li><svg viewBox="0 0 24 24" aria-hidden="true"><path d="M6 2h9l3 3v4H6zM3 10h18v9h-3v3H6v-3H3zm5 6v4h8v-4z"/></svg>555-214-7731</li>
      <li><svg viewBox="0 0 24 24" aria-hidden="true"><path d="M2 5h20v14H2zm2 2v.5l8 5 8-5V7z"/></svg>name@quarrystonedev.com</li>
      <li><svg viewBox="0 0 24 24" aria-hidden="true"><path d="M12 2a10 10 0 1 0 0 20 10 10 0 0 0 0-20zm-1 17.9A8 8 0 0 1 4.2 10L9 15v1c0 1.1.9 2 2 2zm6.9-2.5A2 2 0 0 0 16 16h-1v-3c0-.6-.4-1-1-1H8v-2h2c.6 0 1-.4 1-1V7h2c1.1 0 2-.9 2-2v-.4a8 8 0 0 1 2.9 12.8z"/></svg>www.quarrystonedev.com</li>
    </ul>
  </div>

  <svg class="band" viewBox="0 0 686 13" aria-hidden="true">
    <polygon points="0,0 447,0 443,13 0,13" fill="var(--band-light)"/>
    <polygon points="450,0 686,0 686,13 446,13" fill="var(--band-grey)"/>
  </svg>
</section>

<section class="card card--back" aria-label="Card back">
  <div class="back-mark">
    <span class="back-mark__name">QUARRYSTONE</span>
    <span class="back-mark__sub">DEVELOPMENT GROUP, LLC</span>
  </div>
  <div class="back-url">www.quarrystonedev.com</div>
</section>

</body>
</html>
```